Internet Service Tech provider product flyer redesign - High Rise WIFI

We have created the attached flyer in Word and also attached a PDF. All the content is correct. We just need a complete re-design of the flyer with new relevant hi-res images (based on content) and a more streamlined/cleaner layout.

This product is an entire in-building WIFI system for Body's Corporate in High Rise buildings.

We are a Brisbane-based internet tech company that specialises in providing solutions for High Rise buildings

Body text style - Helvetica Light

Internet

```html
<!DOCTYPE html>
<html lang="en">
<head>
<meta charset="utf-8">
<title>High-Rise WIFI – Flyer</title>
<link rel="stylesheet" href="https://fonts.googleapis.com/css2?family=Roboto:wght@300;400&display=swap">
<style>
  :root {
    --brand-red: #8f1407;
    --band-red: rgba(128, 14, 8, 0.78);
    --label-dark: #2f2c2c;
    --photo-light: #a9adb3;
    --photo-mid: #6b6f76;
    --photo-dark: #2b2d31;
    --white: #ffffff;
  }
  html, body {
    margin: 0;
    padding: 0;
    width: 825px;
    height: 1200px;
    overflow: hidden;
    background: #ffffff;
  }
  .flyer {
    position: relative;
    width: 825px;
    height: 1200px;
    overflow: hidden;
    font-family: "Roboto", "Helvetica Neue", Arial, sans-serif;
    color: var(--white);
  }
  .hero-photo {
    position: absolute;
    left: 0;
    top: 147px;
    width: 825px;
    height: 1053px;
    background:
      linear-gradient(200deg, rgba(255,255,255,0.15) 0%, rgba(0,0,0,0) 40%),
      linear-gradient(180deg, var(--photo-light) 0%, var(--photo-mid) 45%, var(--photo-dark) 100%);
  }
  .signal-waves {
    position: absolute;
    left: 0;
    top: 147px;
    width: 825px;
    height: 700px;
  }
  .header-band {
    position: absolute;
    left: 0;
    top: 0;
    width: 825px;
    height: 147px;
    background: var(--brand-red);
  }
  .title {
    position: absolute;
    left: 40px;
    top: 38px;
    margin: 0;
    font-weight: 300;
    font-size: 56px;
    letter-spacing: -0.5px;
    line-height: 1;
  }
  .audience-label {
    position: absolute;
    left: 40px;
    top: 125px;
    width: 331px;
    height: 51px;
    box-sizing: border-box;
    padding-left: 22px;
    background: var(--label-dark);
    font-weight: 300;
    font-size: 24px;
    line-height: 51px;
  }
  .tone-steps {
    position: absolute;
    left: 390px;
    top: 140px;
    display: flex;
    gap: 12px;
  }
  .tone-steps span {
    width: 24px;
    height: 23px;
    display: block;
  }
  .feature-band {
    position: absolute;
    left: 0;
    top: 1021px;
    width: 825px;
    height: 135px;
    background: var(--band-red);
  }
  .feature-list {
    list-style: none;
    margin: 0;
    padding: 38px 0 0 67px;
    font-weight: 300;
    font-size: 15px;
    line-height: 20.5px;
  }
  .feature-key {
    font-weight: 400;
    margin-right: 10px;
  }
</style>
</head>
<body>
  <main class="flyer">
    <div class="hero-photo" role="img" aria-label="Photograph looking up at an angular glass high-rise tower against a grey cloudy sky"></div>

    <svg class="signal-waves" viewBox="0 0 825 700" aria-hidden="true">
      <g fill="none" stroke="#ffffff" stroke-opacity="0.28" stroke-width="22" stroke-linecap="round">
        <path d="M 330 250 A 70 70 0 0 0 330 340"/>
        <path d="M 418 250 A 70 70 0 0 1 418 340"/>
        <path d="M 290 200 A 130 130 0 0 0 290 390"/>
        <path d="M 458 200 A 130 130 0 0 1 458 390"/>
        <path d="M 240 150 A 200 200 0 0 0 240 440"/>
        <path d="M 508 150 A 200 200 0 0 1 508 440"/>
        <path d="M 190 100 A 270 270 0 0 0 190 490"/>
        <path d="M 558 100 A 270 270 0 0 1 558 490"/>
      </g>
    </svg>

    <header class="header-band">
      <h1 class="title">High-Rise WIFI</h1>
    </header>
    <div class="audience-label">for body's corporate</div>

    <div class="tone-steps" aria-hidden="true">
      <span style="background:#6f6f6f"></span>
      <span style="background:#7a7a7a"></span>
      <span style="background:#858585"></span>
      <span style="background:#909090"></span>
      <span style="background:#9c9c9c"></span>
      <span style="background:#a8a8a8"></span>
      <span style="background:#b4b4b4"></span>
      <span style="background:#c1c1c1"></span>
      <span style="background:#cecece"></span>
      <span style="background:#dbdbdb"></span>
      <span style="background:#e9e9e9"></span>
      <span style="background:#f7f7f7"></span>
    </div>

    <section class="feature-band">
      <ul class="feature-list">
        <li><span class="feature-key">BULK SUPPLY</span>of FNX-type Internet speeds delivered to all residents at wholesale prices</li>
        <li><span class="feature-key">HD WIFI</span>designed specifically for high-rise buildings, using next-generation WIFI technology</li>
        <li><span class="feature-key">AUTOMATED BILLING</span>and payment system that's simple, easy to use and available 24/7</li>
      </ul>
    </section>
  </main>
</body>
</html>
```